We need a cover designed for our book on parenting. The focus of this book is on the parents, not on the child! We like the idea of this title having a double meaning - insight as in gaining insights into parenting, and "in sight" as in looking inward as parents and how to improve ourselves rather than looking outward to improve our children. We would love for the cover to somehow represent this double meaning. I can upload an excerpt from the book soon over the next few days.

Reason: We are still reviewing the amazing designs! Thank you so much! :)

Target Market(s)

Parents with kids of any age from babies through adult children.

Requirements
Must have
• Title is: Harborlight Parenting
• Subtitle is: Steady Homes, Calmer Hearts Ahead
• Authors names: Lena Marsh, LCSW Oscar Marsh, Ph.D.

```html
<!DOCTYPE html>
<html lang="en">
<head>
<meta charset="utf-8">
<title>Harborlight Parenting – Book Cover</title>
<link rel="stylesheet" href="https://fonts.googleapis.com/css2?family=Poppins:wght@500;600;700;800&display=swap">
<style>
  :root {
    --cloud-dark: #7a5042;
    --cloud-rose: #b88672;
    --sun-core: #fffaf0;
    --sky-bright: #fbe6cf;
    --horizon-haze: #e9b994;
    --field-amber: #b0714f;
    --field-mid: #7d4533;
    --field-deep: #3e2119;
    --ink-light: #ffffff;
    --shadow: rgba(40, 18, 10, 0.6);
  }
  * { margin: 0; padding: 0; box-sizing: border-box; }
  html, body {
    width: 800px;
    height: 1200px;
    overflow: hidden;
    background: var(--field-deep);
  }
  .cover {
    position: relative;
    width: 800px;
    height: 1200px;
    overflow: hidden;
    font-family: "Poppins", sans-serif;
    color: var(--ink-light);
  }
  .cover-photo {
    position: absolute;
    inset: 0;
    background:
      /* side vignette */
      radial-gradient(ellipse 620px 900px at 400px 560px, rgba(0,0,0,0) 60%, rgba(50, 22, 14, 0.45) 100%),
      /* sun burst */
      radial-gradient(ellipse 260px 170px at 420px 185px, var(--sun-core) 0%, rgba(255, 245, 228, 0.9) 40%, rgba(251, 230, 207, 0) 100%),
      /* glowing grass tops near horizon */
      radial-gradient(ellipse 520px 150px at 330px 640px, rgba(245, 205, 170, 0.85) 0%, rgba(230, 180, 140, 0) 100%),
      radial-gradient(ellipse 300px 110px at 120px 780px, rgba(214, 150, 110, 0.6) 0%, rgba(214, 150, 110, 0) 100%),
      /* cloud band across top */
      linear-gradient(180deg,
        rgba(110, 70, 56, 0.9) 0px,
        rgba(160, 110, 92, 0.7) 80px,
        rgba(200, 150, 125, 0.35) 140px,
        rgba(200, 150, 125, 0) 190px),
      /* sky, horizon and field */
      linear-gradient(180deg,
        var(--cloud-dark) 0px,
        var(--cloud-rose) 110px,
        var(--sky-bright) 200px,
        #fdebd6 330px,
        #f6d8bb 470px,
        var(--horizon-haze) 530px,
        #d99d74 560px,
        #c98a64 620px,
        var(--field-amber) 700px,
        #9a5c42 820px,
        var(--field-mid) 940px,
        #5b3023 1060px,
        var(--field-deep) 1200px);
  }
  .cover-photo::after {
    /* horizon line of distant land */
    content: "";
    position: absolute;
    left: 0;
    top: 548px;
    width: 800px;
    height: 14px;
    background: linear-gradient(180deg, rgba(190, 130, 100, 0) 0%, rgba(170, 110, 85, 0.45) 50%, rgba(190, 130, 100, 0) 100%);
  }
  .tagline {
    position: absolute;
    top: 38px;
    left: 0;
    width: 100%;
    text-align: center;
    font-weight: 600;
    font-size: 20px;
    letter-spacing: 0.2em;
    text-transform: uppercase;
    text-shadow: 0 1px 4px var(--shadow);
  }
  .title {
    position: absolute;
    left: 0;
    top: 842px;
    width: 100%;
    text-align: center;
    text-transform: uppercase;
    text-shadow: 3px 4px 6px var(--shadow);
  }
  .title-main {
    display: block;
    font-weight: 800;
    font-size: 106px;
    line-height: 1.1;
    letter-spacing: 0.005em;
  }
  .title-sub {
    display: block;
    font-weight: 500;
    font-size: 110px;
    line-height: 1;
    letter-spacing: 0.02em;
  }
  .authors {
    position: absolute;
    bottom: 48px;
    left: 0;
    width: 100%;
    text-align: center;
    font-weight: 700;
    font-size: 32px;
    text-transform: uppercase;
    letter-spacing: 0.01em;
    text-shadow: 2px 2px 4px var(--shadow);
  }
</style>
</head>
<body>
  <main class="cover">
    <div class="cover-photo" role="img" aria-label="Silhouetted couple holding hands in a tall grass field at sunset, warm golden backlight under a cloudy sky"></div>
    <p class="tagline">Steady Homes, Calmer Hearts Ahead</p>
    <h1 class="title">
      <span class="title-main">Harborlight</span>
      <span class="title-sub">Parenting</span>
    </h1>
    <p class="authors">Lena Marsh, LCSW, Oscar Marsh, Ph.D.</p>
  </main>
</body>
</html>
```